Post storm repair flyer

looking for an eye catching 6x9 postcard to send out to single family home owners advertising a "Post Storm Repair Special" explaining that after the recent hurricanes its very important to have your roof checked and any repairs fixed right away before they become a bigger more costly problem and that even though your home wasn't directly hit by the storm the high wind gust could've cause unseen damage.
offer $200 off any repair *some rules may apply
Crest Roofing
877.512.DUNE
www.DuneRoofingco.example

```html
<!DOCTYPE html>
<html lang="en">
<head>
<meta charset="utf-8">
<title>Crest Roofing – Post Storm Repair Special Postcard</title>
<link rel="stylesheet" href="https://fonts.googleapis.com/css2?family=Montserrat:wght@400;500;600;700;800;900&display=swap">
<style>
  :root {
    --gold: #e8b43a;
    --gold-soft: rgba(232, 180, 58, 0.55);
    --ink: #0d0d0d;
    --paper: #ffffff;
    --offer-red: #e0121b;
    --stage: #efece6;
    --rule: #bdbdbd;
  }
  * { box-sizing: border-box; margin: 0; padding: 0; }
  html, body { width: 1200px; height: 1086px; overflow: hidden; }
  body {
    background: var(--stage);
    font-family: "Montserrat", sans-serif;
    color: var(--ink);
    position: relative;
  }
  .postcard {
    position: absolute;
    left: 256px;
    width: 688px;
    height: 464px;
    overflow: hidden;
    background: var(--paper);
    box-shadow: 0 6px 14px rgba(0,0,0,0.25);
  }
  .postcard--front { top: 54px; }
  .postcard--back { top: 563px; height: 465px; }
  .photo { position: absolute; }
  .layer { position: absolute; left: 0; top: 0; }

  /* front */
  .front-photo-top {
    left: 0; top: 0; width: 688px; height: 146px;
    background: linear-gradient(180deg, #9a9a9a 0%, #6e6e6e 45%, #4a4a4a 100%);
  }
  .front-photo-house {
    left: 400px; top: 160px; width: 288px; height: 172px;
    background: linear-gradient(135deg, #e3e3e3 0%, #cfcfcf 60%, #b9b9b9 100%);
  }
  .front-photo-bottom {
    left: 0; top: 345px; width: 688px; height: 119px;
    background: linear-gradient(90deg, #6a6a6a 0%, #8c8c8c 45%, #a5a5a5 70%, #5d5d5d 100%);
  }
  .headline {
    position: absolute; left: 34px; top: 180px;
    font-weight: 900; font-size: 45px; line-height: 0.9;
    letter-spacing: -1.5px; text-transform: uppercase;
  }
  .tagline {
    position: absolute; left: 34px; top: 266px; width: 400px;
    color: var(--paper); font-weight: 600; font-size: 16px; line-height: 1.3;
  }
  .tagline .tagline-strong { font-size: 20px; }
  .phone-bar {
    position: absolute; left: 250px; top: 337px;
    display: flex; align-items: center; gap: 8px;
    color: var(--paper); font-weight: 700; font-size: 21px; letter-spacing: 0.5px;
  }
  .phone-icon { width: 24px; height: 24px; }
  .brand-block {
    position: absolute; left: 520px; top: 178px; width: 130px;
    text-align: center;
  }
  .brand-mark {
    width: 34px; height: 34px; border-radius: 50%;
    background: var(--ink); margin: 0 auto 6px;
  }
  .brand-name { font-weight: 800; font-size: 14px; text-transform: uppercase; }
  .brand-web { font-weight: 500; font-size: 7px; margin-top: 3px; }

  .offer-badge { position: absolute; }
  .offer-badge--front { left: 524px; top: 250px; width: 112px; height: 128px; }
  .offer-badge--back { left: 28px; top: 93px; width: 84px; height: 96px; }
  .offer-text {
    position: absolute; left: 0; width: 100%;
    text-align: center; font-weight: 800; line-height: 1;
  }
  .offer-fine { font-weight: 500; font-style: italic; line-height: 1.05; }

  /* back */
  .back-photo {
    left: 0; top: 0; width: 688px; height: 465px;
    background: linear-gradient(160deg, #9f9f9f 0%, #7a7a7a 40%, #a8a8a8 70%, #6c6c6c 100%);
  }
  .back-heading {
    position: absolute; left: 58px; top: 196px;
    color: var(--gold); font-weight: 600; font-size: 21px; line-height: 1;
  }
  .back-copy {
    position: absolute; left: 58px; top: 250px; width: 240px;
    font-size: 13.5px; line-height: 1.25; font-weight: 500;
  }
  .back-copy p + p { margin-top: 8px; }
  .stamp-box {
    position: absolute; left: 572px; top: 62px; width: 63px; height: 67px;
    border: 1px solid #333;
  }
  .address-line {
    position: absolute; left: 413px; width: 207px; height: 1px;
    background: var(--rule);
  }
  .footer-web {
    position: absolute; left: 104px; top: 404px;
    display: flex; align-items: center; gap: 8px;
    font-weight: 500; font-size: 13px;
  }
  .footer-dot { width: 14px; height: 14px; border-radius: 50%; border: 2px solid var(--ink); }
  .footer-phone {
    position: absolute; left: 412px; top: 400px;
    display: flex; align-items: center; gap: 8px;
    font-weight: 700; font-size: 21px;
  }
</style>
</head>
<body>

<section class="postcard postcard--front">
  <div class="photo front-photo-top" role="img" aria-label="Black and white photo of roofers working on a shingled roof with ladders and shingle bundles"></div>
  <div class="photo front-photo-house" role="img" aria-label="Faded black and white photo of a white house front"></div>
  <div class="photo front-photo-bottom" role="img" aria-label="Black and white photo of a house facade with garage doors and ladders"></div>

  <svg class="layer" width="688" height="464" viewBox="0 0 688 464" aria-hidden="true">
    <rect x="0" y="332" width="688" height="13" fill="var(--paper)"/>
    <polygon points="416,160 440,160 536,332 512,332" fill="var(--gold-soft)"/>
    <polygon points="0,160 416,160 512,332 0,332" fill="var(--gold)"/>
    <polygon points="188,333 510,333 528,375 206,375" fill="var(--ink)"/>
  </svg>

  <h1 class="headline">Post Storm<br>Repair Special</h1>
  <p class="tagline">Protect Your Home. <span class="tagline-strong">Post-Hurricane</span><br><span class="tagline-strong">Roof Inspections</span> is Essential.</p>

  <div class="phone-bar">
    <svg class="phone-icon" viewBox="0 0 24 24" aria-hidden="true">
      <circle cx="12" cy="12" r="10.5" fill="none" stroke="currentColor" stroke-width="2"/>
      <path d="M8.5 6.5l2 0.5 0.8 2.8-1.4 1.2c0.7 1.5 1.8 2.6 3.2 3.2l1.2-1.4 2.8 0.8 0.5 2c-0.5 1-1.5 1.5-2.6 1.3C10.5 16.2 7.8 13.5 7.1 9.1 6.9 8 7.4 7 8.5 6.5z" fill="currentColor"/>
    </svg>
    877.512.DUNE
  </div>

  <div class="brand-block">
    <div class="brand-mark"></div>
    <div class="brand-name">Crest Roofing</div>
    <div class="brand-web">DUNEROOFINGCO.EXAMPLE</div>
  </div>

  <div class="offer-badge offer-badge--front">
    <svg class="layer" width="112" height="128" viewBox="0 0 112 128" aria-hidden="true">
      <polygon points="56,2 110,33 110,95 56,126 2,95 2,33" fill="var(--gold)" stroke="var(--ink)" stroke-width="2.5"/>
      <polygon points="56,24 90,46 80,46 56,32 32,46 22,46" fill="var(--ink)"/>
      <rect x="34" y="20" width="5" height="14" fill="var(--ink)"/>
    </svg>
    <div class="offer-text" style="top:49px;font-size:13px;">Get</div>
    <div class="offer-text" style="top:62px;font-size:20px;color:var(--offer-red);">$200 off</div>
    <div class="offer-text" style="top:83px;font-size:13px;">any repair</div>
    <div class="offer-text offer-fine" style="top:98px;font-size:6.5px;">*some rules<br>may apply</div>
  </div>
</section>

<section class="postcard postcard--back">
  <div class="photo back-photo" role="img" aria-label="Black and white photo of roofers on a two-storey house with ladders against the roof"></div>

  <svg class="layer" width="688" height="465" viewBox="0 0 688 465" aria-hidden="true">
    <polygon points="383,11 403,11 310,145 290,145" fill="var(--gold-soft)"/>
    <polygon points="0,145 314,145 298,165 0,165" fill="var(--ink)"/>
    <polygon points="34,165 298,165 400,31 654,31 654,389 34,389" fill="var(--paper)"/>
    <polygon points="64,389 78,389 40,457 26,457" fill="var(--gold-soft)"/>
    <polygon points="78,389 688,389 688,465 34,465" fill="var(--gold)"/>
  </svg>

  <div class="offer-badge offer-badge--back">
    <svg class="layer" width="84" height="96" viewBox="0 0 84 96" aria-hidden="true">
      <polygon points="42,2 82,25 82,71 42,94 2,71 2,25" fill="var(--gold)" stroke="var(--ink)" stroke-width="2"/>
      <polygon points="42,17 68,34 60,34 42,24 24,34 16,34" fill="var(--ink)"/>
      <rect x="25" y="14" width="4" height="11" fill="var(--ink)"/>
    </svg>
    <div class="offer-text" style="top:36px;font-size:10px;">Get</div>
    <div class="offer-text" style="top:46px;font-size:15px;color:var(--offer-red);">$200 off</div>
    <div class="offer-text" style="top:62px;font-size:10px;">any repair</div>
    <div class="offer-text offer-fine" style="top:73px;font-size:5px;">*some rules<br>may apply</div>
  </div>

  <h2 class="back-heading">Ensure Your Roof’s<br>Safe Today</h2>
  <div class="back-copy">
    <p>After the recent hurricanes, it’s crucial to have your roof inspected and any necessary repairs made promptly.</p>
    <p>Even if your home wasn’t directly hit by the storm, high wind gusts can cause unseen damage.</p>
  </div>

  <div class="stamp-box"></div>
  <div class="address-line" style="top:172px;"></div>
  <div class="address-line" style="top:208px;"></div>
  <div class="address-line" style="top:244px;"></div>
  <div class="address-line" style="top:280px;"></div>
  <div class="address-line" style="top:316px;"></div>

  <div class="footer-web"><span class="footer-dot"></span>DUNEROOFINGCO.EXAMPLE</div>
  <div class="footer-phone">
    <svg class="phone-icon" viewBox="0 0 24 24" aria-hidden="true">
      <circle cx="12" cy="12" r="10.5" fill="none" stroke="currentColor" stroke-width="2"/>
      <path d="M8.5 6.5l2 0.5 0.8 2.8-1.4 1.2c0.7 1.5 1.8 2.6 3.2 3.2l1.2-1.4 2.8 0.8 0.5 2c-0.5 1-1.5 1.5-2.6 1.3C10.5 16.2 7.8 13.5 7.1 9.1 6.9 8 7.4 7 8.5 6.5z" fill="currentColor"/>
    </svg>
    877.512.DUNE
  </div>
</section>

</body>
</html>
```